Cover für ein Taschenbuch zum Thema Ruhestand gesucht!
Zielgruppe
Unsere Zielgruppe sind Senioren, bzw. Menschen im Alter 50+. Es handelt sich bei dem Buch um einen Ratgeber zum Thema 'Ruhestand'. Allerdings wird das Buch ebenso von einer jüngeren Zielgruppe gekauft, da der Ratgeber auch gerne an Eltern oder Großeltern verschenkt wird.
Aufgabenstellung
siehe Dateiupload
Format: 5,25' x 8'

```html
<!DOCTYPE html>
<html lang="de">
<head>
<meta charset="utf-8">
<title>Ihr Ruhestand – Buchcover</title>
<link rel="stylesheet" href="https://fonts.googleapis.com/css2?family=Cinzel:wght@400;600&family=Crimson+Text:ital,wght@0,400;1,700&display=swap">
<style>
  :root {
    --page-bg: #ececea;
    --sky-blue: #1a94c6;
    --sky-mid: #5fb7dc;
    --sky-pale: #eef3ef;
    --sun-glow: #ffd98a;
    --sand-orange: #e8842e;
    --sand-deep: #c9531e;
    --title-white: #ffffff;
    --label-blue: #1d8fc4;
    --ink-dark: #1d1f22;
  }
  * { margin: 0; padding: 0; box-sizing: border-box; }
  html, body {
    width: 1200px;
    height: 3033px;
    overflow: hidden;
    background: var(--page-bg);
  }
  .stage {
    position: relative;
    width: 1200px;
    height: 3033px;
    display: flex;
    align-items: center;
    justify-content: center;
  }
  .book-cover {
    position: relative;
    width: 900px;
    height: 1371px;
    overflow: hidden;
    box-shadow: 0 20px 50px rgba(0, 0, 0, 0.18);
  }
  .cover-photo {
    position: absolute;
    inset: 0;
    background: linear-gradient(
      180deg,
      var(--sky-blue) 0%,
      var(--sky-mid) 26%,
      var(--sky-pale) 50%,
      var(--sun-glow) 68%,
      var(--sand-orange) 84%,
      var(--sand-deep) 100%
    );
  }
  .cover-text {
    position: relative;
    display: flex;
    flex-direction: column;
    align-items: center;
    text-align: center;
    padding-top: 52px;
  }
  .title {
    font-family: "Cinzel", serif;
    font-weight: 600;
    color: var(--title-white);
    line-height: 1.02;
    letter-spacing: 2px;
  }
  .title-line { display: block; font-size: 116px; }
  .subtitle {
    margin-top: 14px;
    font-family: "Cinzel", serif;
    font-weight: 400;
    font-size: 29px;
    letter-spacing: 1px;
    color: var(--title-white);
  }
  .author-label {
    margin-top: 34px;
    padding: 14px 26px;
    background: var(--label-blue);
    font-family: "Crimson Text", serif;
    font-style: italic;
    font-weight: 700;
    font-size: 38px;
    color: var(--title-white);
  }
  .tagline {
    margin-top: 40px;
    font-family: "Crimson Text", serif;
    font-weight: 400;
    font-size: 37px;
    line-height: 1.22;
    color: var(--ink-dark);
  }
</style>
</head>
<body>
  <main class="stage">
    <section class="book-cover">
      <div class="cover-photo" role="img" aria-label="Foto: Paar in Liegestühlen am Strand hält sich bei Sonnenuntergang an den Händen"></div>
      <div class="cover-text">
        <h1 class="title">
          <span class="title-line">IHR</span>
          <span class="title-line">RUHESTAND</span>
        </h1>
        <p class="subtitle">DAS BESTE KOMMT ZUM SCHLUSS!</p>
        <p class="author-label">Konrad Wessling</p>
        <p class="tagline">Die besten Strategien und Tipps, mit denen<br>Sie Ihre Rentenzeit in vollen Zügen<br>genießen können</p>
      </div>
    </section>
  </main>
</body>
</html>
```